holloway paving service

Needs to have phone number 0418259730 and email markholloway@brightmail.com.au.
ABN 62318470915
name mark holloway

For all your concreting solutions
Excavation
Exposed & colour concrete
House & shed slabs
Driveways
Landing & steps

Contact Information for Business Card

ph 0418259730
email markholloway@brightmail.com.au.
ABN 62318470915
name mark holloway

```html
<!DOCTYPE html>
<html lang="en">
<head>
<meta charset="utf-8">
<title>Holloway Paving Service – Business Card</title>
<link href="https://fonts.googleapis.com/css2?family=Oswald:wght@500&family=Roboto+Condensed:wght@400;500&family=Montserrat:wght@600&display=swap" rel="stylesheet">
<style>
  :root {
    --backdrop: #e6e7e9;
    --card: #ffffff;
    --orange: #f26a24;
    --orange-pale: #fbdcc8;
    --grey: #666666;
    --ink: #1a1a1a;
  }
  * { margin: 0; padding: 0; box-sizing: border-box; }
  html, body { width: 1200px; height: 1182px; overflow: hidden; }
  body { background: var(--backdrop); position: relative; font-family: "Roboto Condensed", sans-serif; color: var(--ink); }

  .card { position: absolute; background: var(--card); overflow: hidden; }
  .card--front { left: 216px; top: 94px; width: 768px; height: 450px; }
  .card--back { left: 218px; top: 642px; width: 766px; height: 452px; }

  /* front */
  .brand { position: absolute; left: 37px; top: 76px; display: flex; align-items: center; gap: 14px; }
  .brand__mark { width: 22px; height: 22px; background: var(--orange); }
  .brand__text { border-left: 2px solid var(--orange); padding-left: 12px; }
  .brand__name { font-family: "Montserrat", sans-serif; font-weight: 600; font-size: 18px; color: var(--orange); letter-spacing: 0.2px; line-height: 1.2; }
  .brand__phone { font-family: "Montserrat", sans-serif; font-weight: 600; font-size: 14px; color: var(--orange); letter-spacing: 2px; margin-top: 4px; }

  .contact { position: absolute; left: 37px; top: 279px; display: grid; grid-template-columns: 57px 1fr; font-size: 22px; letter-spacing: -0.3px; line-height: 35px; white-space: nowrap; }
  .contact__labels { border-right: 3px solid var(--orange); }
  .contact__values { padding-left: 10px; }

  .divider { position: absolute; left: 417px; top: 96px; width: 3px; height: 276px; background: var(--ink); }
  .holder-name { position: absolute; left: 454px; top: 236px; font-family: "Oswald", sans-serif; font-weight: 500; font-size: 50px; color: var(--orange); line-height: 1.2; }

  .rule-grey { position: absolute; left: 0; top: 409px; width: 100%; height: 7px; background: var(--grey); }
  .rule-orange { position: absolute; left: 0; top: 422px; width: 100%; height: 28px; background: var(--orange); }

  /* back */
  .decor { position: absolute; left: 500px; top: 230px; width: 300px; height: 300px; border-radius: 50%; background: var(--orange-pale); }
  .edge-grey { position: absolute; left: 726px; top: 0; width: 4px; height: 100%; background: var(--grey); }
  .edge-orange { position: absolute; left: 738px; top: 0; width: 28px; height: 100%; background: var(--orange); }

  .headline { position: absolute; left: 44px; top: 84px; font-family: "Oswald", sans-serif; font-weight: 500; font-size: 43px; color: var(--orange); line-height: 1.2; }
  .services { position: absolute; left: 44px; top: 150px; list-style: none; }
  .services li { display: flex; align-items: center; height: 50.2px; font-family: "Oswald", sans-serif; font-weight: 500; font-size: 30px; }
  .services li::before { content: ""; width: 22px; height: 22px; background: linear-gradient(var(--orange) 50%, var(--grey) 50%); margin: 0 29px 0 5px; }
</style>
</head>
<body>
  <section class="card card--front">
    <div class="brand">
      <div class="brand__mark"></div>
      <div class="brand__text">
        <div class="brand__name">HOLLOWAY PAVING SERVICE</div>
        <div class="brand__phone">0418259730</div>
      </div>
    </div>

    <div class="contact">
      <div class="contact__labels">Ph.<br>Email<br>ABN</div>
      <div class="contact__values">0418259730<br>markholloway@brightmail.com.au.<br>62318470915</div>
    </div>

    <div class="divider"></div>
    <div class="holder-name">Mark Holloway</div>

    <div class="rule-grey"></div>
    <div class="rule-orange"></div>
  </section>

  <section class="card card--back">
    <div class="decor"></div>
    <div class="edge-grey"></div>
    <div class="edge-orange"></div>

    <h2 class="headline">For all concreting solutions</h2>
    <ul class="services">
      <li>Excavation</li>
      <li>Exposed &amp; Colour Concrete</li>
      <li>house &amp; Shed slabs</li>
      <li>Driveways</li>
      <li>Landing &amp; Steps</li>
    </ul>
  </section>
</body>
</html>
```